BRISKEL Need a luxury modern business card designed.

Need a luxury modern business card designed. refer to the uploaded files for the company name and logo in the zip file under source files. i will making my descion on monday. so please send in before then so if we need to edit we will have the time. we have a trade show coming up and im on a deadline for printer.

Target Market(s)

high end clients

Contact Information for Business Card

Company nAme and logo. Tobias Fennick Co-Founder / Project Manager Office # 555-318-7094 Cell # 555-642-1586 BRISKEL.CA Tobias@briskel-example.ca

Font styles to use
Other font styles liked:
• Modern

Requirements
Must have
• Company name and logo, contact info, using the black, gold and white color scheme.

```html
<!DOCTYPE html>
<html lang="en">
<head>
<meta charset="utf-8">
<title>BRISKEL business card</title>
<link href="https://fonts.googleapis.com/css2?family=Josefin+Sans:wght@300&family=Raleway:wght@700&family=Arimo:wght@400&display=swap" rel="stylesheet">
<style>
  :root {
    --backdrop: #e6e6e6;
    --card-white: #ffffff;
    --card-dark: #323232;
    --gold: #a89a62;
    --ink: #1f1f1f;
    --rule: #8a8a8a;
  }
  html, body {
    margin: 0;
    padding: 0;
    width: 1200px;
    height: 1200px;
    overflow: hidden;
    background: var(--backdrop);
  }
  .canvas {
    position: relative;
    width: 1200px;
    height: 1200px;
  }
  .card {
    position: absolute;
    top: 310px;
    height: 594px;
    box-shadow: 0 3px 6px rgba(0,0,0,0.25);
    overflow: hidden;
  }
  .card-front {
    left: 234px;
    width: 364px;
    background: var(--card-white);
  }
  .card-back {
    left: 627px;
    width: 370px;
    background: var(--card-dark);
  }
  .wordmark {
    position: absolute;
    left: 0;
    right: 0;
    text-align: center;
    font-family: "Josefin Sans", sans-serif;
    font-weight: 300;
    letter-spacing: 7px;
    line-height: 1;
  }
  .card-front .wordmark {
    top: 212px;
    font-size: 40px;
    color: var(--ink);
  }
  .card-back .wordmark {
    top: 490px;
    font-size: 42px;
    color: var(--card-white);
  }
  .contact {
    position: absolute;
    left: 0;
    right: 0;
    top: 372px;
    text-align: center;
    font-family: "Arimo", sans-serif;
    color: var(--ink);
  }
  .contact-name {
    font-family: "Raleway", sans-serif;
    font-weight: 700;
    font-size: 21px;
    color: var(--gold);
    margin: 0;
    line-height: 24px;
  }
  .contact-role {
    font-size: 17px;
    margin: 2px 0 0;
    line-height: 22px;
  }
  .icon-row {
    display: flex;
    align-items: center;
    justify-content: center;
    gap: 6px;
    margin-top: 20px;
  }
  .icon-row .rule {
    width: 50px;
    height: 1px;
    background: var(--rule);
    margin: 0 5px;
  }
  .icon {
    width: 24px;
    height: 24px;
    display: block;
  }
  .contact-lines {
    margin: 12px 0 0;
    font-size: 17px;
    line-height: 21px;
  }
  .corner-band {
    position: absolute;
    left: 0;
    top: 0;
  }
</style>
</head>
<body>
<main class="canvas">
  <section class="card card-front" aria-label="Card front">
    <div class="wordmark">BRISKEL</div>
    <div class="contact">
      <p class="contact-name">TOBIAS FENNICK</p>
      <p class="contact-role">Co-Founder / Project Manager</p>
      <div class="icon-row">
        <span class="rule"></span>
        <svg class="icon" viewBox="0 0 24 24" aria-label="Office phone">
          <rect width="24" height="24" rx="2" fill="var(--gold)"/>
          <path d="M6 10 Q12 5 18 10 L16 12 L14 10 L10 10 L8 12 Z" fill="#fff"/>
          <rect x="7" y="12" width="10" height="6" rx="1" fill="#fff"/>
        </svg>
        <svg class="icon" viewBox="0 0 24 24" aria-label="Mobile phone">
          <rect width="24" height="24" rx="2" fill="var(--gold)"/>
          <rect x="8" y="5" width="8" height="14" rx="1.5" fill="none" stroke="#fff" stroke-width="1.5"/>
          <circle cx="12" cy="16.5" r="0.9" fill="#fff"/>
        </svg>
        <svg class="icon" viewBox="0 0 24 24" aria-label="Email">
          <rect width="24" height="24" rx="2" fill="var(--gold)"/>
          <rect x="6" y="8" width="12" height="9" fill="none" stroke="#fff" stroke-width="1.3"/>
          <path d="M6 8 L12 13 L18 8" fill="none" stroke="#fff" stroke-width="1.3"/>
        </svg>
        <span class="rule"></span>
      </div>
      <p class="contact-lines">555-318-7094<br>555-642-1586<br>briskel.ca Tobias@briskel-example.ca</p>
    </div>
  </section>

  <section class="card card-back" aria-label="Card back">
    <svg class="corner-band" width="370" height="594" viewBox="0 0 370 594" aria-hidden="true">
      <polygon points="221,147 370,0 370,296" fill="var(--gold)"/>
    </svg>
    <div class="wordmark">BRISKEL</div>
  </section>
</main>
</body>
</html>
```